Business Card Design for Occupational Medicine Start Up Company

We need to design a professional business card. We are a healthcare company providing occupational medicine services to blue collar industries. We are professional, efficient and high quality service providers.

Target Market(s)

Blue Collar Industry: Shipbuilding, Ports, Trucking Companies; The Executives and Safety Officers for these companies

Industry/Entity Type

Healthcare

Contact Information for Business Card

Logo, Name, Title, Email, Phone

Other font styles liked:
• Please match our Brand Guide

Requirements
Must have
• Our Company Colors and Logo

```html
<!DOCTYPE html>
<html lang="en">
<head>
<meta charset="utf-8">
<title>CrewCare Clinics — Business Card</title>
<link rel="stylesheet" href="https://fonts.googleapis.com/css2?family=Montserrat:wght@400;500;700;800&display=swap">
<style>
  :root {
    --bg: #e9eaee;
    --navy: #2a318c;
    --navy-deep: #232a7a;
    --navy-light: #3a46a6;
    --sky: #1f9ad6;
    --amber: #f4a93a;
    --paper: #ffffff;
    --ink-soft: #6b6d75;
    --ink: #3b3d45;
  }
  * { margin: 0; padding: 0; box-sizing: border-box; }
  html, body { width: 1200px; height: 874px; overflow: hidden; }
  body {
    background: var(--bg);
    font-family: "Montserrat", sans-serif;
    display: flex;
    flex-direction: column;
    align-items: center;
    justify-content: center;
    gap: 40px;
  }
  .card {
    width: 595px;
    height: 340px;
    border-radius: 22px;
    position: relative;
    overflow: hidden;
    box-shadow: 0 6px 18px rgba(20, 24, 60, 0.18);
  }

  /* Back side */
  .card-back { background: var(--navy); }
  .card-back .pattern {
    position: absolute; inset: 0;
    background: linear-gradient(120deg, var(--navy-deep) 0%, var(--navy) 45%, var(--navy-light) 100%);
  }
  .card-back .back-brand {
    position: absolute;
    right: 44px; bottom: 52px;
    display: flex; align-items: center; gap: 10px;
    color: var(--paper);
    font-weight: 700;
    font-size: 16px;
    letter-spacing: 0.5px;
  }
  .back-brand .dot {
    width: 14px; height: 14px; border-radius: 50%;
    background: var(--amber);
  }

  /* Front side */
  .card-front { background: var(--paper); }
  .brand {
    position: absolute;
    left: 48px; top: 42px;
    display: flex; align-items: center; gap: 14px;
  }
  .brand .dot {
    width: 40px; height: 40px; border-radius: 50%;
    background: var(--amber);
  }
  .brand-name {
    color: var(--navy);
    font-weight: 800;
    font-size: 26px;
    line-height: 1;
    letter-spacing: 0.5px;
  }
  .brand-sub {
    color: var(--navy);
    font-weight: 800;
    font-size: 12px;
    letter-spacing: 5px;
    margin-top: 4px;
    padding-left: 46px;
  }
  .edge-tab {
    position: absolute;
    left: 0; top: 146px;
    width: 12px; height: 40px;
    background: var(--amber);
    border-radius: 0 6px 6px 0;
  }
  .person {
    position: absolute;
    left: 56px; top: 146px;
  }
  .person-name {
    color: var(--navy);
    font-weight: 800;
    font-size: 24px;
    letter-spacing: 0.3px;
  }
  .person-title {
    color: var(--ink-soft);
    font-weight: 500;
    font-size: 16px;
    margin-top: 2px;
  }
  .contacts {
    position: absolute;
    left: 56px; top: 234px;
    list-style: none;
    display: flex; flex-direction: column; gap: 6px;
  }
  .contacts li {
    display: flex; align-items: center; gap: 10px;
    color: var(--ink);
    font-size: 15px;
    font-weight: 400;
  }
  .contacts svg { width: 14px; height: 14px; flex: none; }
</style>
</head>
<body>

  <section class="card card-back">
    <div class="pattern" role="img" aria-label="Repeating pattern of the company symbol in tonal navy"></div>
    <div class="back-brand"><span class="dot"></span>CrewCare</div>
  </section>

  <section class="card card-front">
    <div class="brand">
      <span class="dot"></span>
      <div>
        <div class="brand-name">CREWCARE</div>
        <div class="brand-sub">CLINICS</div>
      </div>
    </div>

    <div class="edge-tab"></div>

    <div class="person">
      <div class="person-name">MARK HALVERSEN</div>
      <div class="person-title">President</div>
    </div>

    <ul class="contacts">
      <li>
        <svg viewBox="0 0 24 24" aria-hidden="true"><path fill="var(--sky)" d="M6.6 10.8a15.1 15.1 0 0 0 6.6 6.6l2.2-2.2a1 1 0 0 1 1-.25 11.4 11.4 0 0 0 3.6.57 1 1 0 0 1 1 1V20a1 1 0 0 1-1 1A17 17 0 0 1 3 4a1 1 0 0 1 1-1h3.5a1 1 0 0 1 1 1c0 1.25.2 2.45.57 3.57a1 1 0 0 1-.25 1z"/></svg>
        555-318-4720
      </li>
      <li>
        <svg viewBox="0 0 24 24" aria-hidden="true"><path fill="var(--sky)" d="M2 5h20v14H2z"/><path fill="none" stroke="#fff" stroke-width="1.8" d="M2.5 5.5 12 13l9.5-7.5"/></svg>
        mark@crewcareclinics.com
      </li>
      <li>
        <svg viewBox="0 0 24 24" aria-hidden="true"><circle cx="12" cy="12" r="10" fill="var(--sky)"/><path fill="none" stroke="#fff" stroke-width="1.4" d="M2 12h20M12 2c3 3 3 17 0 20M12 2c-3 3-3 17 0 20"/></svg>
        www.crewcareclinics.com
      </li>
    </ul>
  </section>

</body>
</html>
```